Business Card Design Project

After recently finishing a design project for the company logo using markbazaar, it's now time for a business card. Attached to this is the logo.

The requirements for the business card are pretty straightforward:

- A clean, uncomplicated look
- Consistent usage of fonts
- Designs for both single sided and double sided cards
- A modern layout with preferably space to refer to social media accounts and/or downloadable vcards through a qr code
- consistent application of the company colour scheme: red/white. Hex codes for exact colour can be provided

Thanks!

```html
<!DOCTYPE html>
<html lang="en">
<head>
<meta charset="utf-8">
<title>Stone Arch Staffing – Business Card</title>
<link rel="stylesheet" href="https://fonts.googleapis.com/css2?family=Open+Sans:wght@400;600;700&display=swap">
<style>
  :root {
    --backdrop: #e9e6e2;
    --card: #ffffff;
    --ink: #231f20;
    --grey: #8a8a8a;
    --red: #e21f26;
    --black: #231f20;
  }
  * { margin: 0; padding: 0; box-sizing: border-box; }
  html, body {
    width: 960px; height: 1200px; overflow: hidden;
    background: var(--backdrop);
    font-family: "Open Sans", Arial, sans-serif;
    color: var(--ink);
  }
  .canvas { position: relative; width: 960px; height: 1200px; }

  .card {
    position: absolute;
    background: var(--card);
    border-radius: 28px;
    overflow: hidden;
  }
  .card--front { left: 48px; top: 88px; width: 840px; height: 480px; }
  .card--back  { left: 55px; top: 638px; width: 840px; height: 480px; }

  .wordmark {
    font-weight: 600;
    color: var(--ink);
    letter-spacing: -1px;
    white-space: nowrap;
  }
  .card--front .wordmark {
    position: absolute; left: 48px; top: 48px;
    font-size: 52px; line-height: 1;
  }

  .contact { position: absolute; left: 46px; top: 210px; }
  .contact__name { font-size: 24px; font-weight: 700; line-height: 1; margin-bottom: 22px; }
  .contact__role { font-size: 20px; font-weight: 400; }
  .contact__line {
    display: flex; align-items: center; gap: 8px;
    font-size: 22px; line-height: 1; margin-bottom: 18px;
  }
  .contact__line svg { width: 16px; height: 16px; fill: var(--ink); }
  .contact__address { font-size: 22px; line-height: 32px; margin-top: 6px; }

  .brand-block {
    position: absolute; left: 560px; top: 150px;
    width: 230px; height: 230px;
    background: var(--red);
  }

  .stripe { position: absolute; bottom: 0; left: 0; width: 100%; height: 20px; display: flex; }
  .stripe__black { width: 254px; background: var(--black); }
  .stripe__red   { width: 331px; background: var(--red); }
  .stripe__grey  { flex: 1; background: var(--grey); }

  .lockup {
    position: absolute; left: 140px; top: 180px;
    display: flex; align-items: center; gap: 24px;
  }
  .lockup__mark { width: 70px; height: 70px; background: var(--red); }
  .card--back .wordmark { font-size: 62px; line-height: 1; }
</style>
</head>
<body>
<main class="canvas">

  <section class="card card--front">
    <div class="wordmark">Stone Arch Staffing</div>

    <div class="contact">
      <p class="contact__name">Your Name - <span class="contact__role">Designation</span></p>
      <p class="contact__line">
        <svg viewBox="0 0 16 16" aria-hidden="true"><path d="M3 2h3l1.5 3.5-2 1.2a8 8 0 0 0 3.8 3.8l1.2-2L14 10v3a1 1 0 0 1-1 1A12 12 0 0 1 2 3a1 1 0 0 1 1-1z"/></svg>
        123-123-1234
      </p>
      <p class="contact__line">
        <svg viewBox="0 0 16 16" aria-hidden="true"><path d="M1 3h14v10H1z M2.2 4.2v.4L8 9l5.8-4.4v-.4z M2.2 6v5.8h11.6V6L8 10.4z" fill-rule="evenodd"/></svg>
        info@yourwebsite.com
      </p>
      <p class="contact__line">
        <svg viewBox="0 0 16 16" aria-hidden="true"><circle cx="8" cy="8" r="6.5"/></svg>
        www.stonearch.com
      </p>
      <p class="contact__address">1234, Street Name, City<br>District, Country Code.</p>
    </div>

    <div class="brand-block"></div>

    <div class="stripe">
      <span class="stripe__black"></span>
      <span class="stripe__red"></span>
      <span class="stripe__grey"></span>
    </div>
  </section>

  <section class="card card--back">
    <div class="lockup">
      <span class="lockup__mark"></span>
      <span class="wordmark">Stone Arch Staffing</span>
    </div>
  </section>

</main>
</body>
</html>
```